Health Care Company with Logo Needs Business Cards designed

We are a luxury behavioral health company looking for business cards design we already have a logo and are looking for someone to design a sophisticated luxurious looking business card. Please note that Card design should be captivating just like the logo and also encompass the logo color

Industry/Entity Type

Healthcare

Contact Information for Business Card

Logo,company name, tagline, my name and title, contact details, and physical address

```html
<!DOCTYPE html>
<html lang="en">
<head>
<meta charset="UTF-8">
<title>Willowmere Wellness Partners – Business Card</title>
<link href="https://fonts.googleapis.com/css2?family=Roboto+Condensed:wght@400;700&display=swap" rel="stylesheet">
<style>
  :root {
    --page-bg: #dfe6ee;
    --card-bg: #f7f8fa;
    --purple: #6b3f8f;
    --blue: #1a8fd6;
    --deep-blue: #1468c0;
    --orange: #e8822a;
    --text: #3d3d3d;
  }
  html, body {
    margin: 0;
    width: 1200px;
    height: 900px;
    overflow: hidden;
    background: var(--page-bg);
    font-family: "Roboto Condensed", "Arial Narrow", sans-serif;
  }
  .card {
    position: absolute;
    left: 100px;
    top: 165px;
    width: 1000px;
    height: 570px;
    background: var(--card-bg);
    box-shadow: 0 6px 24px rgba(40, 60, 90, 0.18);
    overflow: hidden;
  }
  .card-accent {
    position: absolute;
    inset: 0;
  }
  .brand {
    position: absolute;
    left: 56px;
    top: 60px;
    display: flex;
    align-items: center;
    gap: 20px;
  }
  .brand-square {
    width: 64px;
    height: 64px;
    background: var(--orange);
  }
  .brand-name {
    margin: 0;
    font-size: 42px;
    font-weight: 400;
    color: var(--text);
    line-height: 1;
  }
  .brand-tagline {
    margin: 9px 0 0 2px;
    font-size: 15px;
    font-weight: 400;
    letter-spacing: 2px;
    color: var(--blue);
  }
  .person-name {
    position: absolute;
    left: 54px;
    top: 200px;
    margin: 0;
    font-size: 35px;
    font-weight: 700;
    color: var(--purple);
    text-transform: uppercase;
  }
  .person-title {
    position: absolute;
    left: 54px;
    top: 253px;
    margin: 0;
    font-size: 25px;
    color: var(--text);
  }
  .address {
    position: absolute;
    left: 54px;
    top: 318px;
    margin: 0;
    font-style: normal;
    font-size: 25px;
    line-height: 36px;
    color: var(--text);
  }
  .contacts {
    position: absolute;
    left: 54px;
    top: 424px;
    margin: 0;
    padding: 0;
    list-style: none;
    font-size: 25px;
    line-height: 36px;
    color: var(--text);
  }
  .contacts li {
    display: flex;
    align-items: center;
    gap: 10px;
  }
  .contacts svg {
    width: 20px;
    height: 20px;
    flex: none;
  }
</style>
</head>
<body>
  <div class="card">
    <svg class="card-accent" viewBox="0 0 1000 570" aria-hidden="true">
      <polygon points="874,0 1000,0 1000,275 815,275" fill="var(--orange)"/>
      <polygon points="865,294 960,294 943,570 703,570" fill="var(--deep-blue)"/>
    </svg>

    <div class="brand">
      <div class="brand-square"></div>
      <div>
        <h1 class="brand-name">Willowmere Wellness Partners</h1>
        <p class="brand-tagline">Compassionate care for lasting wellbeing</p>
      </div>
    </div>

    <h2 class="person-name">Daniel Harlow</h2>
    <p class="person-title">President</p>

    <address class="address">
      1840 Seacliff Harbor Dr<br>
      Bayview CA 92000
    </address>

    <ul class="contacts">
      <li>
        <svg viewBox="0 0 20 20" aria-hidden="true"><path d="M5 2 L8 2 L9 6 L7 8 Q9 12 12 13 L14 11 L18 12 L18 15 Q17 18 14 18 Q3 16 2 5 Q2 2 5 2 Z" fill="var(--deep-blue)"/></svg>
        <span>555-240-0187</span>
      </li>
      <li>
        <svg viewBox="0 0 20 20" aria-hidden="true"><rect x="2" y="5" width="16" height="11" fill="var(--orange)"/><polyline points="2,5 10,11 18,5" fill="none" stroke="#fff" stroke-width="1.5"/></svg>
        <span>info@willowmerewellness.com</span>
      </li>
      <li>
        <svg viewBox="0 0 20 20" aria-hidden="true"><circle cx="10" cy="10" r="7.5" fill="none" stroke="var(--purple)" stroke-width="1.6"/><ellipse cx="10" cy="10" rx="3.2" ry="7.5" fill="none" stroke="var(--purple)" stroke-width="1.4"/><line x1="2.5" y1="10" x2="17.5" y2="10" stroke="var(--purple)" stroke-width="1.4"/></svg>
        <span>www.willowmerewellness.com</span>
      </li>
    </ul>
  </div>
</body>
</html>
```